Communication and Marketing agency needs a new presentation card

We are a group of communication and marketing agencies specialized in companies that are in the logistics and industrial sector. The head agency is TELVANO Grupo and the group consists of 4 agencies: TELVANO Media, TELVANO Digital, TELVANO Research and DifundeEnPantalla. We hace 4 offices in Spain (Madrid, Barcelona, Valencia and Murcia). We are looking for a clean and attractive design that transmits our experience, brand presence in the market and knowledge to those who receive the card.It has to maintain the colors of the logo that is attached.
Target Market(s)
logistics and industrial sector
Marketing department
Contact Information for Business Card
Clean and attractive design

```html
<!DOCTYPE html>
<html lang="es">
<head>
<meta charset="utf-8">
<title>TELVANO Grupo – Tarjeta de presentación</title>
<link rel="stylesheet" href="https://fonts.googleapis.com/css2?family=Roboto:wght@400;500;700&display=swap">
<style>
  :root {
    --brand-red: #b31b27;
    --ink: #111111;
    --text-grey: #555555;
    --rule-grey: #c9c9c9;
    --paper: #ffffff;
    --backdrop: #e3e3e3;
  }
  * { box-sizing: border-box; margin: 0; padding: 0; }
  html, body {
    width: 1125px; height: 1200px; overflow: hidden;
    background: var(--backdrop);
    font-family: "Roboto", Arial, sans-serif;
  }
  .canvas { position: relative; width: 1125px; height: 1200px; }

  .card {
    position: absolute; left: 171px; width: 826px; height: 472px;
  }
  .card--front { top: 106px; background: var(--paper); }
  .card--back { top: 639px; background: var(--brand-red); color: var(--paper); }

  /* Front */
  .front-brand {
    position: absolute; right: calc(826px - 368px); top: 196px;
    text-align: right; color: var(--brand-red); font-weight: 500;
    line-height: 1;
  }
  .front-brand__name { display: block; font-size: 46px; letter-spacing: 1px; }
  .front-brand__unit { display: block; font-size: 28px; margin-top: 6px; }

  .divider {
    position: absolute; left: 409px; top: 129px; width: 1px; height: 219px;
    background: var(--rule-grey);
  }

  .contact { position: absolute; left: 445px; top: 130px; }
  .contact__name {
    font-size: 30px; font-weight: 700; color: var(--brand-red); line-height: 1;
  }
  .contact__role {
    font-size: 20px; font-weight: 500; color: var(--ink); margin-top: 6px;
  }
  .contact__list { list-style: none; margin-top: 20px; }
  .contact__item {
    display: flex; align-items: center; height: 26.3px;
    font-size: 20px; color: var(--text-grey);
  }
  .contact__icon {
    width: 18px; height: 18px; margin-right: 13px; flex: none;
    fill: var(--brand-red);
  }

  .offices {
    position: absolute; left: 0; right: 0; top: 406px;
    text-align: center; font-size: 20px; color: var(--text-grey);
  }
  .offices__dot {
    display: inline-block; width: 7px; height: 7px; border-radius: 50%;
    background: var(--brand-red); margin: 0 7px; vertical-align: middle;
  }

  /* Back */
  .group-brand {
    position: absolute; left: 0; right: 0; top: 160px;
    display: flex; justify-content: center;
  }
  .group-brand__inner { text-align: right; font-weight: 500; line-height: 1; }
  .group-brand__name { display: block; font-size: 82px; letter-spacing: 3px; }
  .group-brand__unit { display: block; font-size: 46px; margin-top: 10px; }

  .back-rule {
    position: absolute; left: 32px; right: 32px; top: 363px;
    height: 1px; background: rgba(255,255,255,0.8);
  }

  .agencies {
    position: absolute; left: 0; right: 0; top: 392px;
    list-style: none;
  }
  .agency {
    position: absolute; top: 0; transform: translateX(-50%);
    text-align: right; font-weight: 500; line-height: 1; white-space: nowrap;
  }
  .agency__name { display: block; font-size: 27px; letter-spacing: 0.5px; }
  .agency__unit { display: block; font-size: 18px; margin-top: 5px; }
  .agency--digital { left: 111px; }
  .agency--media { left: 319px; }
  .agency--research { left: 524px; }
  .agency--video { left: 723px; text-align: left; }
  .agency--video .agency__name { font-size: 22px; }
</style>
</head>
<body>
<main class="canvas">

  <section class="card card--front" aria-label="Anverso de la tarjeta">
    <div class="front-brand">
      <span class="front-brand__name">TELVANO</span>
      <span class="front-brand__unit">Media</span>
    </div>

    <div class="divider"></div>

    <div class="contact">
      <h1 class="contact__name">Lucía Ortegal</h1>
      <p class="contact__role">Director</p>
      <ul class="contact__list">
        <li class="contact__item">
          <svg class="contact__icon" viewBox="0 0 24 24" aria-hidden="true"><path d="M6.6 10.8a15.1 15.1 0 0 0 6.6 6.6l2.2-2.2c.3-.3.7-.4 1-.2 1.1.4 2.3.6 3.6.6.6 0 1 .4 1 1V20c0 .6-.4 1-1 1C10.6 21 3 13.4 3 4c0-.6.4-1 1-1h3.5c.6 0 1 .4 1 1 0 1.3.2 2.5.6 3.6.1.3 0 .7-.2 1z"/></svg>
          910 555 274
        </li>
        <li class="contact__item">
          <svg class="contact__icon" viewBox="0 0 24 24" aria-hidden="true"><path d="M7 1h10a2 2 0 0 1 2 2v18a2 2 0 0 1-2 2H7a2 2 0 0 1-2-2V3a2 2 0 0 1 2-2zm0 3v14h10V4zm5 15.5a1 1 0 1 0 0 2 1 1 0 0 0 0-2z"/></svg>
          600 555 418
        </li>
        <li class="contact__item">
          <svg class="contact__icon" viewBox="0 0 24 24" aria-hidden="true"><path d="M2 5h20v14H2zm2 2v.5l8 5 8-5V7l-8 5z"/></svg>
          lortegal@telvano.es
        </li>
        <li class="contact__item">
          <svg class="contact__icon" viewBox="0 0 24 24" aria-hidden="true"><rect x="3" y="3" width="18" height="18" rx="2"/></svg>
          luciaortegal
        </li>
        <li class="contact__item">
          <svg class="contact__icon" viewBox="0 0 24 24" aria-hidden="true"><path d="M12 2a10 10 0 1 0 0 20 10 10 0 0 0 0-20zm0 2c1 0 2.4 2.1 2.9 5H9.1C9.6 6.1 11 4 12 4zM4.3 10h3.9a18 18 0 0 0 0 4H4.3a8 8 0 0 1 0-4zm4.8 5h5.8c-.5 2.9-1.9 5-2.9 5s-2.4-2.1-2.9-5zm6.7-1a18 18 0 0 0 0-4h3.9a8 8 0 0 1 0 4z"/></svg>
          telvano.es
        </li>
      </ul>
    </div>

    <p class="offices">
      Madrid<span class="offices__dot"></span>Barcelona<span class="offices__dot"></span>Valencia<span class="offices__dot"></span>Murcia
    </p>
  </section>

  <section class="card card--back" aria-label="Reverso de la tarjeta">
    <div class="group-brand">
      <div class="group-brand__inner">
        <span class="group-brand__name">TELVANO</span>
        <span class="group-brand__unit">Grupo</span>
      </div>
    </div>

    <div class="back-rule"></div>

    <ul class="agencies">
      <li class="agency agency--digital"><span class="agency__name">TELVANO</span><span class="agency__unit">Digital</span></li>
      <li class="agency agency--media"><span class="agency__name">TELVANO</span><span class="agency__unit">Media</span></li>
      <li class="agency agency--research"><span class="agency__name">TELVANO</span><span class="agency__unit">Research</span></li>
      <li class="agency agency--video"><span class="agency__name">DIFUNDE</span><span class="agency__name">ENPANTALLA</span></li>
    </ul>
  </section>

</main>
</body>
</html>
```